Law Firm in Texas in need of new letterhead

Law Firm in Fort Worth, TX, USA named "Pell & Varnum, Attorneys-At-Law, LLP." This is a general practice law firm that mostly does Family Law and Criminal Defense work.

We are looking for a new letterhead that has a "classical" appeal, with modern elements.

Any color combination is fine, but please note that we do fax many documents, so the design must be clearly legible in Black and White.

We would like our letterhead to project a sense of professionalism, integrity, and ability.

Target Market(s)

Letterhead will be for correspondence generally with other attorneys and clients.

Industry/Entity Type

Law Firm

Logo Text

Pell & Varnum, Attorneys-At-Law, LLP.

Logo styles of interest
Pictorial/Combination Logo
Wordmark Logo
Lettermark Logo
Requirements
Nice to have
• Although not necessary, a "Texas Star" that is incorporated into the design would be a nice touch.
Should not have
• Colors that do not convert to B&W easily

```html
<!DOCTYPE html>
<html lang="en">
<head>
<meta charset="utf-8">
<title>Pell &amp; Varnum Letterhead</title>
<link rel="stylesheet" href="https://fonts.googleapis.com/css2?family=Cinzel:wght@400;600&family=Tinos:wght@400;700&family=Questrial&display=swap">
<style>
  :root {
    --backdrop: #d9d9d9;
    --paper: #fbfbfb;
    --navy: #2b4f7c;
    --grey-text: #7d7d7d;
    --body-text: #3a3a3a;
    --rule: #9a9a9a;
    --star-tone: #ececec;
  }
  * { margin: 0; padding: 0; box-sizing: border-box; }
  html, body { width: 1200px; height: 1000px; overflow: hidden; }
  body {
    background: var(--backdrop);
    display: flex;
    justify-content: center;
    align-items: center;
    gap: 50px;
  }
  .sheet {
    position: relative;
    width: 540px;
    height: 764px;
    background: var(--paper);
    box-shadow: 0 4px 14px rgba(0,0,0,0.12);
  }
  .masthead {
    position: absolute;
    top: 52px;
    left: 0;
    right: 0;
    text-align: center;
    color: var(--navy);
    font-family: "Cinzel", serif;
  }
  .masthead .firm-name {
    font-size: 27px;
    font-weight: 400;
    letter-spacing: 1px;
  }
  .masthead .firm-sub {
    display: flex;
    align-items: center;
    justify-content: center;
    gap: 8px;
    font-size: 11.5px;
    letter-spacing: 1.2px;
    margin-top: 2px;
  }
  .masthead .firm-sub::before,
  .masthead .firm-sub::after {
    content: "";
    width: 26px;
    height: 1px;
    background: var(--navy);
  }
  .star-watermark {
    position: absolute;
    top: 180px;
    left: 90px;
    width: 360px;
    height: 320px;
    background: radial-gradient(circle, var(--star-tone) 0%, rgba(236,236,236,0.4) 55%, rgba(251,251,251,0) 75%);
  }
  .partners {
    position: absolute;
    top: 515px;
    right: 44px;
    width: 210px;
    padding-right: 12px;
    border-right: 1px solid var(--rule);
    text-align: right;
    font-family: "Tinos", serif;
    color: var(--grey-text);
    font-size: 8.5px;
    line-height: 1.3;
  }
  .partners .partner-name {
    font-size: 11px;
    letter-spacing: 0.5px;
    text-transform: uppercase;
  }
  .partners .partner-role { margin-bottom: 4px; }
  .partners .partner + .partner { margin-top: 8px; }
  .web {
    position: absolute;
    right: 44px;
    bottom: 78px;
    font-family: "Tinos", serif;
    font-weight: 700;
    font-size: 9px;
    color: var(--navy);
  }
  .footer {
    position: absolute;
    left: 44px;
    bottom: 40px;
    display: flex;
    align-items: center;
    gap: 12px;
    font-family: "Tinos", serif;
    font-weight: 700;
    font-size: 9px;
    color: var(--navy);
    line-height: 1.3;
  }
  .footer .divider {
    width: 1px;
    height: 24px;
    background: var(--navy);
  }
  .letter-body {
    position: absolute;
    top: 170px;
    left: 60px;
    right: 60px;
    font-family: "Questrial", sans-serif;
    font-size: 10.5px;
    line-height: 1.55;
    color: var(--body-text);
  }
  .letter-body p { margin-bottom: 12px; }
  .sign-off {
    position: absolute;
    top: 400px;
    right: 60px;
    text-align: right;
    font-family: "Questrial", sans-serif;
    color: var(--body-text);
  }
  .sign-off .closing { font-size: 10.5px; margin-bottom: 10px; }
  .sign-off .row { display: flex; align-items: center; gap: 16px; }
  .signature-area {
    width: 120px;
    height: 40px;
    background: linear-gradient(90deg, #e6ebf3, #dfe6f0);
  }
  .sign-off .signer { font-size: 11px; font-weight: 600; }
</style>
</head>
<body>

  <section class="sheet sheet--blank">
    <header class="masthead">
      <div class="firm-name">Pell &amp; Varnum</div>
      <div class="firm-sub">Attorneys At Law, LLP</div>
    </header>
    <div class="star-watermark" role="img" aria-label="Large faint five-pointed Texas star watermark"></div>
    <aside class="partners">
      <div class="partner">
        <div class="partner-name">Daniel Pell</div>
        <div class="partner-role">Managing Partner</div>
        <div>- Licensed in the State of Texas</div>
        <div>- U.S. District Court</div>
        <div>(Northern District of Texas)</div>
        <div>- United States Supreme Court</div>
      </div>
      <div class="partner">
        <div class="partner-name">Laura Jean Varnum</div>
        <div>- Licensed in the State of Texas</div>
        <div>- U.S. District Court</div>
        <div>(Northern District of Texas)</div>
      </div>
    </aside>
    <div class="web">www.pell-varnum.com</div>
    <footer class="footer">
      <div class="address">1840 W. Harlow Ave.<br>Fort Worth, TX 76107</div>
      <div class="divider"></div>
      <div class="contact">Phone: (817) 555-0148<br>Fax: (817) 555-0193</div>
    </footer>
  </section>

  <section class="sheet sheet--letter">
    <header class="masthead">
      <div class="firm-name">Pell &amp; Varnum</div>
      <div class="firm-sub">Attorneys At Law, LLP</div>
    </header>
    <div class="letter-body">
      <p>Thank you for meeting with our office this week. We have reviewed the documents you provided and prepared a summary of the next steps in your matter.</p>
      <p>Please review the enclosed forms and return them signed before the hearing date so we can file them with the court.</p>
      <p>Feel free to call our office with any questions.</p>
      <p>We look forward to working with you.</p>
    </div>
    <div class="sign-off">
      <div class="closing">Yours Sincerely,</div>
      <div class="row">
        <div class="signature-area" role="img" aria-label="Handwritten signature in blue ink"></div>
        <div class="signer">Nora Ellison</div>
      </div>
    </div>
    <aside class="partners">
      <div class="partner">
        <div class="partner-name">Daniel Pell</div>
        <div class="partner-role">Managing Partner</div>
        <div>- Licensed in the State of Texas</div>
        <div>- U.S. District Court</div>
        <div>(Northern District of Texas)</div>
        <div>- United States Supreme Court</div>
      </div>
      <div class="partner">
        <div class="partner-name">Laura Jean Varnum</div>
        <div>- Licensed in the State of Texas</div>
        <div>- U.S. District Court</div>
        <div>(Northern District of Texas)</div>
      </div>
    </aside>
    <div class="web">www.pell-varnum.com</div>
    <footer class="footer">
      <div class="address">1840 W. Harlow Ave.<br>Fort Worth, TX 76107</div>
      <div class="divider"></div>
      <div class="contact">Phone: (817) 555-0148<br>Fax: (817) 555-0193</div>
    </footer>
  </section>

</body>
</html>
```